Company Website for Varnoth Signal, an open source data analytics company focused on relationship and li

I need a company/brand website for our new startup, Varnoth Signal LLC. We are a company focused on using life pattern analysis techniques, looking at relationships and how relationships, attributes, and activity cluster to infer aggregate information about individuals and groups. Our focus is on improving the digital advertising market.

We have a company logo which I will upload shortly.

Target Market(s)

Digital Advertising

Number of Pages Required

3 page

Font styles to use
Sans Serif

Requirements
Must have
• An main page, about us, contact page.
Nice to have
• Varnoth Signal relies on state of the art analytics applied to a the digital marketing space. While it is heavy in science, we also understand the art of influence. The website should have a scientific edge but also a flair that illustrates our focus on applying the hard science and analytics to influencing the behavior of people.

```html
<!DOCTYPE html>
<html lang="en">
<head>
<meta charset="utf-8">
<title>Varnoth Signal</title>
<link href="https://fonts.googleapis.com/css2?family=Montserrat:wght@400;500;600;700&display=swap" rel="stylesheet">
<style>
:root{
  --blue:#2a79c9;
  --blue-bright:#3a8be0;
  --dark:#232323;
  --darker:#1c1c1c;
  --white:#ffffff;
  --muted:#cfcfcf;
  --hero-a:#5a5450;
  --hero-b:#2e2a28;
}
*{margin:0;padding:0;box-sizing:border-box}
html,body{width:741px;height:1200px;overflow:hidden;background:var(--dark)}
body{font-family:'Montserrat',sans-serif;color:var(--white);position:relative}
.abs{position:absolute}

.hero{left:0;top:0;width:741px;height:403px;background:linear-gradient(120deg,#7b746e 0%,var(--hero-a) 35%,var(--hero-b) 100%)}
.brand{left:73px;top:16px;display:flex;align-items:center;gap:6px;font-weight:700;font-size:15px;color:var(--blue-bright)}
.brand-dot{width:10px;height:10px;background:#f0a020;border-radius:50%}
.nav{right:114px;top:22px;display:flex;justify-content:flex-end;gap:12px;font-size:7.8px;font-weight:500;white-space:nowrap}
.nav a{color:var(--white);text-decoration:none}
.nav a.active{color:var(--blue-bright);border-bottom:1px solid var(--blue-bright);padding-bottom:3px}
.cart{left:637px;top:20px;width:13px;height:13px;border-radius:50%;background:var(--blue)}
.search{left:656px;top:23px}
.tagline{left:74px;top:155px;width:344px;height:36px;border:1.5px solid var(--white);font-weight:700;font-size:17px;display:flex;align-items:center;justify-content:center;letter-spacing:.3px}
.headline{left:73px;top:196px;font-weight:700;font-size:29px;line-height:39px;letter-spacing:.3px}
.cta{left:74px;top:277px;width:108px;height:26px;background:var(--blue);font-size:9.5px;font-weight:700;letter-spacing:1px;display:flex;align-items:center;justify-content:center}
.arrow{top:198px}
.dots{left:353px;top:357px;display:flex;gap:3px}
.dots span{width:6px;height:6px;border-radius:50%;background:var(--white)}
.dots span:first-child{background:var(--blue-bright)}

.why{left:0;top:403px;width:741px;height:64px;background:var(--dark);display:flex;align-items:center;justify-content:center;font-size:24px;font-weight:500;letter-spacing:1px}
.tabs{left:0;top:467px;width:741px;height:32px;background:var(--darker);border-bottom:1px solid #333}
.tab{top:0;height:32px;font-size:7.5px;font-weight:500;display:flex;align-items:center;justify-content:center;border-left:1px solid #3a3a3a;white-space:nowrap}

.network{left:69px;top:532px;width:293px;height:100px;background:linear-gradient(90deg,#eef2f6,#dfe7ef)}
.market-title{left:69px;top:646px;font-size:17.5px;font-weight:500;letter-spacing:.4px;white-space:nowrap}
.market-text{left:70px;top:672px;width:292px;font-size:6.2px;line-height:12.4px;color:var(--muted)}
.num{left:377px;width:37px;height:37px;border-radius:50%;background:var(--blue);display:flex;align-items:center;justify-content:center;font-size:18px}
.point{left:428px;width:240px}
.point h3{font-size:6.6px;font-weight:500;color:var(--blue-bright);margin-bottom:6px}
.point p{font-size:6px;line-height:12.3px;color:var(--muted)}

.services{left:0;top:782px;width:741px;height:281px;background:linear-gradient(100deg,#2f6fb5,#3a82cf 50%,#2d70bb)}
.tile{top:861px;width:121px;height:120px;border:1px solid rgba(255,255,255,.8);display:flex;align-items:center;justify-content:center}
.tile-label{top:993px;width:70px;height:25px;border:1.5px solid var(--white);font-size:7.5px;font-weight:600;letter-spacing:.8px;display:flex;align-items:center;justify-content:center}

.footer{left:0;top:1063px;width:741px;height:110px;background:var(--dark)}
.foot-col{top:1094px;font-size:6.4px;line-height:12.5px}
.foot-col h4{font-size:7px;font-weight:500;color:var(--blue-bright);margin-bottom:8px}
.foot-col b{font-weight:600}
.blue{color:var(--blue-bright)}
.socials{left:70px;top:1127px;display:flex;gap:7px}
.socials span{width:16px;height:16px;border:1px solid #777;border-radius:50%}
.email-field{left:481px;top:1141px;width:89px;height:16px;border:1px solid #666;border-radius:8px;font-size:6.4px;color:#999;padding-left:9px;display:flex;align-items:center}
.bottom{left:0;top:1173px;width:741px;height:27px;background:var(--darker);display:flex;justify-content:center;align-items:center}
</style>
</head>
<body>

<section class="abs hero" role="img" aria-label="Photo of business people shaking hands"></section>
<div class="abs brand"><span class="brand-dot"></span>Varnoth Signal</div>
<nav class="abs nav">
  <a class="active" href="#">Home</a><a href="#">About us</a><a href="#">Our Team</a><a href="#">Our Products</a><a href="#">Blog</a><a href="#">Contact</a>
</nav>
<div class="abs cart"></div>
<svg class="abs search" width="8" height="8" viewBox="0 0 8 8"><circle cx="3.2" cy="3.2" r="2.3" fill="none" stroke="#fff" stroke-width="1.2"/><line x1="5" y1="5" x2="7.5" y2="7.5" stroke="#fff" stroke-width="1.2"/></svg>

<div class="abs tagline">BECAUSE YOUR TIME IS VALUABLE</div>
<h1 class="abs headline">TAP INTO THE POWER OF<br>SOCIAL MEDIA.</h1>
<div class="abs cta">OUR PRODUCTS</div>
<svg class="abs" style="left:74px;top:303px" width="10" height="8"><polygon points="0,0 10,0 0,8" fill="#1d5a99"/></svg>
<svg class="abs arrow" style="left:25px" width="12" height="20" viewBox="0 0 12 20"><polyline points="10,2 2,10 10,18" fill="none" stroke="#fff" stroke-width="2.5"/></svg>
<svg class="abs arrow" style="left:698px" width="12" height="20" viewBox="0 0 12 20"><polyline points="2,2 10,10 2,18" fill="none" stroke="#fff" stroke-width="2.5"/></svg>
<div class="abs dots"><span></span><span></span><span></span></div>
<svg class="abs" style="left:346px;top:384px" width="41" height="20"><polygon points="0,20 20.5,0 41,20" fill="#2a79c9"/><polyline points="17,10 20.5,13 24,10" fill="none" stroke="#fff" stroke-width="1"/></svg>

<h2 class="abs why">WHY WE ARE DIFFERENT</h2>
<div class="abs tabs">
  <div class="abs tab" style="left:68px;width:83px">Our Story</div>
  <div class="abs tab" style="left:151px;width:70px">Mission &amp; Vision</div>
  <div class="abs tab" style="left:221px;width:72px;border-right:1px solid #3a3a3a">Company Values</div>
</div>

<div class="abs network" role="img" aria-label="Illustration of a connected social network of people"></div>
<h2 class="abs market-title">DIGITAL ADVERTISING MARKET</h2>
<p class="abs market-text">Lorem ipsum dolor sit amet, consectetur adipiscing elit. Aenean egestas eu leo nec eleifend. Nulla sapien turpis, convallis ac ultrices sed, aliquam sit amet arcu. Phasellus est orci, biben-dum consequat quam sit amet, facilisis pharetra nisl. Nullam ultrices mi quam, et volutpat magna suscipit eget.</p>

<div class="abs num" style="top:530px">1</div>
<div class="abs point" style="top:533px"><h3>DUMMY TEXT OF THE PRINTING AND TYPESETTING</h3><p>Consectetur adipiscing elit. Pellentesque ut mollis lectus. Ut ultricies lacinia feugiat. Cras sed enim quis nunc condimentum ullamcorper. Aliquam eget lorem at purus porta volutpat in in enim. Fusce sollicitudin pulvinar rutrum. Etiam tempus porta mauris at fermentum.</p></div>
<div class="abs num" style="top:614px">2</div>
<div class="abs point" style="top:616px"><h3>DUMMY TEXT OF THE PRINTING AND TYPESETTING</h3><p>Consectetur adipiscing elit. Pellentesque ut mollis lectus. Ut ultricies lacinia feugiat. Cras sed enim quis nunc condimentum ullamcorper. Aliquam eget lorem at purus porta volutpat in in enim.</p></div>
<div class="abs num" style="top:692px">3</div>
<div class="abs point" style="top:694px"><h3>DUMMY TEXT OF THE PRINTING AND TYPESETTING</h3><p>Consectetur adipiscing elit. Pellentesque ut mollis lectus. Ut ultricies lacinia feugiat. Cras sed enim quis nunc condimentum ullamcorper. Aliquam eget lorem at purus porta volutpat in in enim.</p></div>

<section class="abs services" role="img" aria-label="Blue-tinted photo of people reviewing charts at a desk"></section>
<div class="abs tile" style="left:89px">
  <svg width="52" height="44" viewBox="0 0 52 44" fill="none" stroke="#fff" stroke-width="2.5"><polygon points="26,3 49,14 26,25 3,14"/><polyline points="3,22 26,33 49,22"/><polyline points="3,30 26,41 49,30"/></svg>
</div>
<div class="abs tile" style="left:233px">
  <svg width="56" height="46" viewBox="0 0 56 46" fill="none" stroke="#fff" stroke-width="2.5"><rect x="4" y="24" width="7" height="16"/><rect x="14" y="16" width="7" height="24"/><polyline points="6,16 18,8 28,12 42,2"/><polyline points="36,2 42,2 42,8"/><circle cx="34" cy="28" r="9"/><line x1="40" y1="35" x2="48" y2="43"/><line x1="2" y1="42" x2="30" y2="42"/></svg>
</div>
<div class="abs tile" style="left:383px">
  <svg width="52" height="42" viewBox="0 0 52 42" fill="none" stroke="#fff" stroke-width="2.8"><path d="M16 32H12a9 9 0 0 1 0-18 13 13 0 0 1 25-3 10 10 0 0 1 3 21h-4"/><line x1="26" y1="17" x2="26" y2="30"/><line x1="26" y1="35" x2="26" y2="39"/></svg>
</div>
<div class="abs tile" style="left:532px">
  <svg width="54" height="46" viewBox="0 0 54 46" fill="#fff"><circle cx="16" cy="18" r="5"/><path d="M7 34a9 9 0 0 1 18 0z"/><circle cx="38" cy="18" r="5"/><path d="M29 34a9 9 0 0 1 18 0z"/><path d="M12 8a18 18 0 0 1 26 0" fill="none" stroke="#fff" stroke-width="2"/><polygon points="40,4 41,11 34,9"/><path d="M42 40a18 18 0 0 1-26 0" fill="none" stroke="#fff" stroke-width="2"/><polygon points="14,44 13,37 20,39"/></svg>
</div>
<div class="abs tile-label" style="left:115px">DATA</div>
<div class="abs tile-label" style="left:258px">ANANLYTICS</div>
<div class="abs tile-label" style="left:408px">RISK</div>
<div class="abs tile-label" style="left:557px">INFLUENCE</div>

<footer class="abs footer"></footer>
<div class="abs foot-col" style="left:70px"><b>Copyright 2017-18 <span class="blue">Varnoth Signal</span></b><br><b>Designed and development by Northgate Studio</b></div>
<div class="abs socials"><span></span><span></span><span></span><span></span></div>
<div class="abs foot-col" style="left:275px;top:1091px"><h4>Our location</h4><b>Harlow Ridge LLC 0000 Teller Ave,<br>Suite 112 Brookmoor, IL 00000</b><br><b>Phone : +00 1 55501234</b><br><b>Email : info@varnothsignal.com</b></div>
<div class="abs foot-col" style="left:481px;top:1091px"><h4>Kepp in touch</h4><b>Lorem ipsum dolor sit amet, consectetur adi sollicitud<br>ante tellus ornare mi, et mollis</b></div>
<div class="abs email-field">Your email</div>
<svg class="abs" style="left:557px;top:1145px" width="7" height="7" viewBox="0 0 7 7"><polyline points="0,3.5 6,3.5" stroke="#999" stroke-width="1.2"/><polyline points="3.5,1 6,3.5 3.5,6" fill="none" stroke="#999" stroke-width="1.2"/></svg>
<div class="abs bottom"><svg width="12" height="8" viewBox="0 0 12 8"><polyline points="1,7 6,2 11,7" fill="none" stroke="#fff" stroke-width="2"/></svg></div>

</body>
</html>
```